RW Framewell Inc Business cards

We need business cards using our existing logo but slightly modified. Right now the logo says RW Loadbearing Masonry. We want to keep the RW part of the design, but replace the Structural Concrete portion with "FRAMEWELL". Please see the attached file.
Ideally this would be a blank template so we can add Different Names, titles, and phone numbers later.
On the one side we want only the logo and on the other side the detail. I'm attaching an example for you to see.
Please reach out with any other questions. Our address and other details will be given out once we find a design we like.

Target Market(s)

Construction Industry

```html
<!DOCTYPE html>
<html lang="en">
<head>
<meta charset="utf-8">
<title>RW Framewell Inc – Business Cards</title>
<link rel="stylesheet" href="https://fonts.googleapis.com/css2?family=Roboto:wght@400;500;700&display=swap">
<style>
  :root {
    --backdrop: #5a86c4;
    --brand-blue: #2f63a8;
    --brand-blue-deep: #24518e;
    --card-white: #f4f4f3;
    --text-grey: #555a60;
    --decor-grey: #e6e6e6;
    --white: #ffffff;
  }
  * { margin: 0; padding: 0; box-sizing: border-box; }
  html, body { width: 1200px; height: 852px; overflow: hidden; }
  body {
    background: var(--backdrop);
    font-family: "Roboto", Arial, sans-serif;
    position: relative;
  }
  .card {
    position: absolute;
    width: 525px;
    height: 300px;
    border-radius: 22px;
    overflow: hidden;
    box-shadow: 0 6px 14px rgba(20, 40, 80, 0.35);
  }
  /* Logo side */
  .card--back {
    left: 90px;
    top: 110px;
    background: var(--brand-blue);
    display: flex;
    align-items: center;
    justify-content: center;
  }
  .card--back .wordmark {
    color: var(--brand-blue-deep);
    font-size: 54px;
    font-weight: 500;
    letter-spacing: 3px;
  }
  /* Detail side */
  .card--front {
    left: 585px;
    top: 430px;
    background: var(--card-white);
  }
  .card--front .decor-square {
    position: absolute;
    right: 120px;
    top: 30px;
    width: 150px;
    height: 150px;
    background: var(--decor-grey);
  }
  .card--front .wordmark {
    position: absolute;
    right: 34px;
    top: 50px;
    color: var(--brand-blue);
    font-size: 34px;
    font-weight: 500;
    letter-spacing: 1px;
  }
  .holder {
    position: absolute;
    left: 36px;
    top: 118px;
  }
  .holder .name {
    color: var(--brand-blue);
    font-size: 21px;
    font-weight: 700;
  }
  .holder .title {
    color: var(--text-grey);
    font-size: 14px;
    margin-top: 3px;
  }
  .contacts {
    position: absolute;
    left: 36px;
    bottom: 30px;
    list-style: none;
    color: var(--text-grey);
    font-size: 14px;
    line-height: 1.45;
  }
  .contacts li { display: flex; align-items: flex-start; gap: 10px; }
  .contacts svg { width: 13px; height: 13px; margin-top: 3px; flex: none; fill: var(--brand-blue); }
  .contacts .no-icon { padding-left: 23px; }
  .web-tab {
    position: absolute;
    right: 0;
    bottom: 36px;
    width: 245px;
    height: 44px;
    background: var(--brand-blue);
    border-top-left-radius: 22px;
    color: var(--white);
    font-size: 14px;
    font-weight: 700;
    display: flex;
    align-items: center;
    padding-left: 38px;
  }
</style>
</head>
<body>
  <section class="card card--back" aria-label="Logo side">
    <span class="wordmark">RW Framewell</span>
  </section>

  <section class="card card--front" aria-label="Detail side">
    <div class="decor-square" aria-hidden="true"></div>
    <span class="wordmark">RW Framewell</span>

    <div class="holder">
      <p class="name">Mark RW Ellison</p>
      <p class="title">Managing Director</p>
    </div>

    <ul class="contacts">
      <li>
        <svg viewBox="0 0 16 16" aria-hidden="true"><path d="M3.6 1.5l2.3 2.3-1.4 1.9c.9 2 2.4 3.6 4.4 4.6l1.9-1.4 2.5 2.3-1.3 2.6C7.6 13.6 2.4 8.4 1 3z"/></svg>
        <span>555-014-2290</span>
      </li>
      <li>
        <svg viewBox="0 0 16 16" aria-hidden="true"><path d="M1 3h14v10H1z M1.8 3.8L8 8.6l6.2-4.8" stroke="#f4f4f3" stroke-width="1.2"/></svg>
        <span>mark@framewellinc.com</span>
      </li>
      <li class="no-icon"><span>58 Sample Road, Any Town,<br>Oregon, US 97001</span></li>
    </ul>

    <div class="web-tab">www.framewellinc.com</div>
  </section>
</body>
</html>
```